Become a Mentor - For Musicians, Artists, Producers and Teachers

Here is the full creative brief:

https://files.quorvant.com/sheets/d/7kTbWmQa2_pLRz9XcN4eHs8JuYd3FoVgA6iBnCqE/view?mode=shared

Here is the background image file: https://www.stashvel.com/sh/48kdmwtnb7yrs2p/AAZm3kLPQwTx8VnHRe4jBcDu?dl=0

LOGO:
https://www.stashvel.com/sh/k382fubotn7wq6/AAJhT5LsRy2D-mKzPX9CvGhNb?dl=0

```html
<!DOCTYPE html>
<html lang="en">
<head>
<meta charset="utf-8">
<title>Become a Mentor – Campaign Layouts</title>
<link rel="stylesheet" href="https://fonts.googleapis.com/css2?family=Open+Sans:wght@300&family=Passion+One:wght@700&family=Tinos:wght@400;700&display=swap">
<style>
  :root {
    --board: #2a2726;
    --white: #ffffff;
    --label: #f2f2f2;
    --purple-deep: #1c0636;
    --purple: #4a1590;
    --purple-glow: #7a2fd0;
    --photo-light: #b9b2aa;
    --photo-mid: #6e625a;
    --photo-dark: #2b2321;
  }
  * { box-sizing: border-box; margin: 0; padding: 0; }
  html, body { width: 1200px; height: 926px; overflow: hidden; background: var(--board); }
  .board { position: relative; width: 1200px; height: 926px; background: var(--board); }

  .layout { position: absolute; overflow: hidden; color: var(--white); }
  .layout > * { position: absolute; }

  .photo {
    inset: 0;
    background:
      radial-gradient(ellipse at 70% 25%, var(--photo-mid), transparent 60%),
      linear-gradient(100deg, var(--photo-light) 0%, var(--photo-mid) 35%, var(--photo-dark) 75%);
  }
  .tint { inset: 0; }

  .kicker { font-family: "Tinos", serif; font-weight: 400; white-space: nowrap; }
  .headline-top { font-family: "Passion One", sans-serif; font-weight: 700; letter-spacing: 0.28em; line-height: 1; white-space: nowrap; }
  .headline-main { font-family: "Passion One", sans-serif; font-weight: 700; letter-spacing: 0.03em; line-height: 1; white-space: nowrap; }
  .intro { font-family: "Tinos", serif; line-height: 1.3; }
  .apply {
    border: 2px solid var(--white);
    font-family: "Tinos", serif; font-weight: 700;
    display: flex; align-items: center; justify-content: center;
    white-space: nowrap;
  }
  .contact { font-family: "Tinos", serif; letter-spacing: 0.06em; white-space: nowrap; }

  .brand { display: flex; align-items: center; gap: 5px; font-family: "Tinos", serif; font-weight: 700; color: var(--white); white-space: nowrap; }
  .brand-dot { border-radius: 50%; background: var(--white); flex: none; }

  .label { position: absolute; font-family: "Open Sans", sans-serif; font-weight: 300; color: var(--label); white-space: nowrap; }

  /* Print poster */
  .poster { left: 110px; top: 24px; width: 358px; height: 463px; }
  .poster .tint { background: linear-gradient(180deg, transparent 40%, rgba(60,16,120,.75) 62%, var(--purple-deep) 100%), radial-gradient(ellipse at 75% 80%, var(--purple-glow), transparent 55%); opacity: .95; }
  .poster .brand-top { left: 128px; top: 36px; font-size: 12px; }
  .poster .kicker { left: 20px; top: 227px; font-size: 16px; }
  .poster .headline-top { left: 20px; top: 254px; font-size: 33px; }
  .poster .headline-main { left: 20px; top: 288px; font-size: 54px; }
  .poster .intro { left: 22px; top: 342px; font-size: 9.5px; }
  .poster .apply { left: 23px; top: 380px; width: 165px; height: 40px; font-size: 23px; font-weight: 400; }
  .poster .brand-bottom { left: 250px; top: 394px; font-size: 9px; }
  .poster .contact { left: 23px; top: 437px; font-size: 11px; }

  /* Instagram square */
  .square { left: 600px; top: 67px; width: 317px; height: 317px; }
  .square .tint { background: linear-gradient(180deg, transparent 35%, rgba(60,16,120,.7) 62%, var(--purple-deep) 100%), radial-gradient(ellipse at 70% 85%, var(--purple-glow), transparent 55%); }
  .square .kicker { left: 19px; top: 150px; font-size: 11.5px; }
  .square .headline-top { left: 19px; top: 170px; font-size: 24px; }
  .square .headline-main { left: 19px; top: 196px; font-size: 41px; }
  .square .intro { left: 21px; top: 238px; font-size: 7px; }
  .square .brand-side { left: 213px; top: 242px; font-size: 8px; }
  .square .apply { left: 22px; top: 266px; width: 122px; height: 30px; font-size: 17px; font-weight: 400; }
  .square .contact-phone { left: 171px; top: 263px; font-size: 14px; }
  .square .contact-web { left: 160px; top: 282px; font-size: 7px; letter-spacing: .05em; }

  /* Facebook cover */
  .cover { left: 110px; top: 545px; width: 850px; height: 324px; }
  .cover .photo { right: auto; width: 520px; }
  .cover .tint { background: linear-gradient(90deg, transparent 0%, transparent 48%, var(--purple) 62%, var(--purple-deep) 100%), radial-gradient(ellipse at 72% 55%, var(--purple-glow), transparent 50%); }
  .cover .text-block { left: 520px; top: 0; width: 260px; height: 324px; }
  .cover .text-block > * { position: absolute; left: 0; right: 0; text-align: center; }
  .cover .kicker { top: 33px; font-size: 17px; font-weight: 700; }
  .cover .headline-top { top: 60px; font-size: 34px; }
  .cover .headline-main { top: 96px; font-size: 52px; }
  .cover .intro { top: 158px; font-size: 14.5px; line-height: 1.2; }
  .cover .apply { left: 10px; right: auto; top: 226px; width: 229px; height: 56px; font-size: 32px; }
  .cover .contact { left: 470px; top: 289px; font-size: 12.5px; font-weight: 700; }
  .cover .brand-center { left: 372px; top: 176px; font-size: 12px; }
</style>
</head>
<body>
<main class="board">

  <section class="layout poster" aria-label="Print poster">
    <div class="photo" role="img" aria-label="Photo of a mentor and student talking in a recording studio beside a mixing desk and speaker"></div>
    <div class="tint"></div>
    <div class="brand brand-top"><span class="brand-dot" style="width:10px;height:10px"></span>Meridian Academy of Sound</div>
    <p class="kicker">START YOUR CAREER TODAY</p>
    <h1 class="headline-top">BECOME A</h1>
    <h2 class="headline-main">MENTOR</h2>
    <p class="intro">Turn your skills and passion for music into a career<br>Designed for Musicians, Artists, Producers &amp; Teachers</p>
    <div class="apply">APPLY NOW</div>
    <div class="brand brand-bottom"><span class="brand-dot" style="width:7px;height:7px"></span>Meridian Academy<br>of Sound</div>
    <p class="contact">Call 1300 555 019 &nbsp;| &nbsp;www.meridianacademyofsound.com.au</p>
  </section>
  <p class="label" style="left:377px;top:500px;font-size:22px">A4/A3/A5</p>

  <section class="layout square" aria-label="Instagram post">
    <div class="photo" role="img" aria-label="Photo of a mentor and student talking in a recording studio"></div>
    <div class="tint"></div>
    <p class="kicker">START YOUR CAREER TODAY</p>
    <h1 class="headline-top">BECOME A</h1>
    <h2 class="headline-main">MENTOR</h2>
    <p class="intro">Turn your skills and passion for music into a career<br>Designed for Musicians, Artists, Producers &amp; Teachers</p>
    <div class="brand brand-side"><span class="brand-dot" style="width:7px;height:7px"></span>Meridian Academy<br>of Sound</div>
    <div class="apply">APPLY NOW</div>
    <p class="contact contact-phone">Call 1300 555 019</p>
    <p class="contact contact-web">www.meridianacademyofsound.com.au</p>
  </section>
  <p class="label" style="left:756px;top:392px;font-size:30px">INSTAGRAM</p>

  <section class="layout cover" aria-label="Facebook cover">
    <div class="photo" role="img" aria-label="Photo of a mentor and student seated in a recording studio with mixing desk and monitors"></div>
    <div class="tint"></div>
    <div class="brand brand-center"><span class="brand-dot" style="width:9px;height:9px"></span>Meridian Academy<br>of Sound</div>
    <div class="text-block">
      <p class="kicker">START YOUR CAREER TODAY</p>
      <h1 class="headline-top">BECOME A</h1>
      <h2 class="headline-main">MENTOR</h2>
      <p class="intro">Turn your skills and passion for music<br>into a career Designed for Musicians,<br>Artists, Producers &amp; Teachers</p>
      <div class="apply">APPLY NOW</div>
    </div>
    <p class="contact">Call 1300 555 019 &nbsp;| &nbsp;www.meridianacademyofsound.com.au</p>
  </section>
  <p class="label" style="left:435px;top:882px;font-size:24px">FACEBOOK COVER</p>

</main>
</body>
</html>
```